TL - business card

Tallow Partners is an insurance brokerage firm, inovative, proactive, vigorous, which aims to become the leader of the insurance brokers in Anfrica. We should like to get some designs which should be avoided also in Gray / Metallic for the Administration and Orange / Blue for the Managers (ike in the picture sent). The Blue / Green logo is not the correct one, but the source of the file. Please adjust the color accordingly for the business cards. 1 / Orange / Blue 2 / Gray / Metallic We want something classic but which is transmitted strenght, inovation, modernity and most of all, rapidity. We want something start-up like, very punchy and catching eye remaining profesional at the same time. Name: Dorian Whitlock Function: Managing Director Address: N ° 17/18 Rua Veloso - R / C 2B Direita - Bairro Mutamba - Luanda Tel: (+244) 947 582 316 Email: dorian.whitlock@tallow-p.example Website: www.tallow-p. example We want classic in the front and creative, colorfull at the back. The cards will be printed in relief, with very high quality of paper.
Insurance Broker
Colors
Designer to choose colors to be used in the design.

```html
<!DOCTYPE html>
<html lang="en">
<head>
<meta charset="utf-8">
<title>Tallow Partners – Business Card</title>
<link rel="stylesheet" href="https://fonts.googleapis.com/css2?family=Lato:wght@400;700&display=swap">
<style>
  :root {
    --backdrop: #2e2926;
    --paper: #fbfbfa;
    --orange: #f06a22;
    --blue: #27a6e1;
    --ink: #3a3a3a;
    --rule: #c9c9c9;
    --white: #ffffff;
  }
  * { box-sizing: border-box; margin: 0; padding: 0; }
  html, body { width: 1200px; height: 844px; overflow: hidden; }
  body {
    background: var(--backdrop);
    font-family: "Lato", Arial, sans-serif;
    display: flex;
    align-items: center;
    justify-content: center;
    gap: 50px;
  }
  .card {
    width: 540px;
    height: 310px;
    border-radius: 4px;
    position: relative;
    overflow: hidden;
    box-shadow: 0 10px 30px rgba(0,0,0,.45);
  }

  /* Front */
  .card-front { background: var(--paper); color: var(--ink); }
  .brand {
    position: absolute;
    top: 52px;
    right: 40px;
    display: flex;
    align-items: center;
    gap: 14px;
  }
  .brand-dot {
    width: 46px; height: 46px;
    border-radius: 50%;
    border: 4px solid var(--blue);
  }
  .brand-name {
    font-weight: 700;
    font-size: 24px;
    letter-spacing: .5px;
    color: var(--orange);
    text-transform: uppercase;
  }
  .brand-rule {
    position: absolute;
    top: 130px; right: 40px;
    width: 300px;
    border-top: 1px solid var(--rule);
  }
  .contact {
    position: absolute;
    left: 36px;
    bottom: 34px;
  }
  .person-name {
    font-size: 21px;
    font-weight: 400;
    text-transform: uppercase;
    letter-spacing: .3px;
    line-height: 1;
  }
  .person-name .first { color: var(--orange); }
  .person-name .last { color: var(--blue); }
  .person-role { font-size: 13px; margin-top: 3px; }
  .contact-line { font-size: 12.5px; margin-top: 14px; }
  .label { font-weight: 700; }
  .label-phone { color: var(--orange); }
  .label-email { color: var(--blue); }
  .sep { color: var(--ink); margin: 0 4px; }
  .address { font-size: 12.5px; margin-top: 12px; }

  /* Back */
  .card-back { background: var(--blue); }
  .back-split { position: absolute; inset: 0; width: 100%; height: 100%; }
  .back-brand {
    position: absolute;
    inset: 0;
    display: flex;
    align-items: center;
    justify-content: center;
    font-weight: 700;
    font-size: 30px;
    letter-spacing: 1px;
    text-transform: uppercase;
    color: var(--white);
  }
</style>
</head>
<body>
  <section class="card card-front" aria-label="Business card front">
    <div class="brand">
      <span class="brand-dot" aria-hidden="true"></span>
      <span class="brand-name">Tallow Partners</span>
    </div>
    <div class="brand-rule"></div>
    <div class="contact">
      <p class="person-name"><span class="first">Dorian</span> <span class="last">Whitlock</span></p>
      <p class="person-role">Managing Director</p>
      <p class="contact-line">
        <span class="label label-phone">P:</span> (+244) 947 582 316
        <span class="sep">|</span>
        <span class="label label-email">E:</span> dorian.whitlock@tallow-p.example
      </p>
      <p class="address">N ° 17/18 Rua Veloso - R / C 2B Direita - Bairro Mutamba - Luanda</p>
    </div>
  </section>

  <section class="card card-back" aria-label="Business card back">
    <svg class="back-split" viewBox="0 0 540 310" preserveAspectRatio="none" aria-hidden="true">
      <polygon points="0,0 300,0 240,310 0,310" fill="var(--orange)"/>
    </svg>
    <div class="back-brand">Tallow Partners</div>
  </section>
</body>
</html>
```